Business Card Design for BrightvaleMedia.com

--I need a business card design for my company BrightvaleMedia.com

I have attached my logo...I want the brightvale media logo on the front of the business card, and then I want The Quillstone Chief on the back of it with my information.

I would like to see a light colored background as well as a dark colored background

FRONT:
BRIGHTVALE MEDIA LOGO
248 N. Larkmoor
3rd Floor
San Diego CA 92173
www.BrightvaleMedia.com

Advanced Website & App Development
Websites, Apps, Online Voucher Systems

Leading Edge Marketing Services
SMS, VB, SMM, SEM,

BACK:
QUILLSTONE CHIEF LOGO
Dorian Pelletta
The Quillstone Chief
Call Or Text: 619-555-0148
Dorian@QuillstoneChief.example
www.QuillstoneChief.example

Target Market(s)

small business owners

Industry/Entity Type

Business Consultant

Contact Information for Business Card

FRONT:
BRIGHTVALE MEDIA LOGO
248 N. Larkmoor
3rd Floor
San Diego CA 92173
www.BrightvaleMedia.com

SMS, VB, SMM, SEM,

BACK:
QUILLSTONE CHIEF LOGO
Dorian Pelletta
The Quillstone Chief
Dorian@QuillstoneChief.example
www.QuillstoneChief.example

Requirements
Must have
• add this quote on it somewhere, anywhere,preferrably on back
• "The Fastest Way To Success Is To Take Action”
• — Dorian Pelletta, Quillstone Chief
Nice to have
• open
Should not have
• red

```html
<!DOCTYPE html>
<html lang="en">
<head>
<meta charset="utf-8">
<title>Brightvale Media Business Card</title>
<link rel="stylesheet" href="https://fonts.googleapis.com/css2?family=Source+Sans+3:wght@400;600;700&display=swap">
<style>
  :root {
    --stage: #4b4b4b;
    --brand-blue: #0472ae;
    --card-white: #ffffff;
    --ink-grey: #555555;
    --quote-grey: #7a7a7a;
    --rule-grey: #c9c9c9;
    --tab-grey: #6a6a6a;
  }
  * { margin: 0; padding: 0; box-sizing: border-box; }
  html, body {
    width: 1105px; height: 1200px; overflow: hidden;
    background: var(--stage);
    font-family: "Source Sans 3", "Myriad Pro", Arial, sans-serif;
  }
  .canvas { position: relative; width: 1105px; height: 1200px; }
  .card { position: absolute; left: 196px; width: 720px; height: 411px; }

  /* Front */
  .card-front {
    top: 146px; background: var(--brand-blue); color: var(--card-white);
    text-align: center;
  }
  .front-wordmark {
    position: absolute; top: 92px; left: 0; right: 0;
    font-size: 40px; font-weight: 600; letter-spacing: 3px; line-height: 48px;
  }
  .front-details { position: absolute; top: 170px; left: 0; right: 0; font-size: 19.5px; line-height: 26px; }
  .front-details .site { font-weight: 700; }
  .front-details .group { margin-top: 14px; }

  /* Back */
  .card-back { top: 602px; background: var(--card-white); overflow: hidden; }
  .back-wordmark {
    position: absolute; left: 50px; top: 196px; width: 290px; text-align: center;
    font-size: 27px; font-weight: 700; letter-spacing: 1.5px;
    color: var(--brand-blue);
  }
  .divider {
    position: absolute; left: 362px; top: 126px; width: 1px; height: 163px;
    background: var(--rule-grey);
  }
  .contact { position: absolute; left: 384px; top: 126px; }
  .contact .name { font-size: 27px; font-weight: 600; color: var(--brand-blue); line-height: 34px; }
  .contact .title { font-size: 20px; color: var(--ink-grey); line-height: 26px; margin-bottom: 12px; }
  .contact ul { list-style: none; }
  .contact li {
    display: flex; align-items: center; gap: 10px;
    font-size: 19.5px; color: var(--ink-grey); line-height: 28px;
  }
  .contact svg { width: 17px; height: 17px; flex: none; fill: var(--brand-blue); }

  .quote {
    position: absolute; left: 0; right: 0; top: 330px;
    text-align: center; font-size: 15px; line-height: 20px; color: var(--quote-grey);
  }
  .quote cite { font-style: normal; color: var(--brand-blue); font-weight: 600; }

  .tabs { position: absolute; left: 0; right: 0; bottom: 0; height: 13px; display: flex; gap: 3px; }
  .tab { flex: 1; border-radius: 8px 8px 0 0; background: var(--brand-blue); }
  .tab.mid { background: var(--tab-grey); }
</style>
</head>
<body>
<div class="canvas">
  <section class="card card-front" aria-label="Card front">
    <div class="front-wordmark">BRIGHTVALE MEDIA</div>
    <div class="front-details">
      <p>248 N. Larkmoor, 3rd Floor, San Diego CA 92173</p>
      <p class="site">www.BrightvaleMedia.com</p>
      <div class="group">
        <p>Advanced Website &amp; App Development</p>
        <p>Websites &bull; Apps &bull; Online Voucher Systems</p>
      </div>
      <div class="group">
        <p>Leading Edge Marketing Services</p>
        <p>SMS &bull; VB &bull; SMM &bull; SEM</p>
      </div>
    </div>
  </section>

  <section class="card card-back" aria-label="Card back">
    <div class="back-wordmark">QUILLSTONE CHIEF</div>
    <div class="divider"></div>
    <div class="contact">
      <p class="name">Dorian Pelletta</p>
      <p class="title">The Quillstone Chief</p>
      <ul>
        <li>
          <svg viewBox="0 0 24 24" aria-hidden="true"><path d="M6.6 10.8a15.1 15.1 0 0 0 6.6 6.6l2.2-2.2a1 1 0 0 1 1-.25 11.4 11.4 0 0 0 3.6.57 1 1 0 0 1 1 1V20a1 1 0 0 1-1 1A17 17 0 0 1 3 4a1 1 0 0 1 1-1h3.5a1 1 0 0 1 1 1c0 1.25.2 2.45.57 3.57a1 1 0 0 1-.25 1z"/></svg>
          619-555-0148
        </li>
        <li>
          <svg viewBox="0 0 24 24" aria-hidden="true"><path d="M2 5h20v2l-10 6L2 7z"/><path d="M2 9l10 6 10-6v10H2z"/></svg>
          Dorian@QuillstoneChief.example
        </li>
        <li>
          <svg viewBox="0 0 24 24" aria-hidden="true"><circle cx="12" cy="12" r="10"/><path d="M12 2v20M2 12h20M5 6c4 2 10 2 14 0M5 18c4-2 10-2 14 0" stroke="#fff" stroke-width="1.4" fill="none"/></svg>
          www.QuillstoneChief.example
        </li>
      </ul>
    </div>
    <blockquote class="quote">
      &ldquo;The Fastest Way To Success Is To Take Action&rdquo; &mdash; <cite>Dorian Pelletta, Quillstone Chief</cite>
    </blockquote>
    <div class="tabs">
      <div class="tab"></div>
      <div class="tab mid"></div>
      <div class="tab"></div>
    </div>
  </section>
</div>
</body>
</html>
```